Web Design for a Biotech Consulting Firm

We need a web site design for a new business based in Philadelphia called Verantel Dx. This is a consulting firm that will serve medical diagnostics industry, which is part of the life science/healthcare industry focusing on developing and marketing products that help in early detection, monitoring or management of diseases. Our consulting firm will help medical diagnostic companies to overcome key challenges in designing, evaluating and marketing new products.Our company name is Verantel Dx. Verantel is Latin word for "something" Dx represents diagnostics. The idea behind the name is that we help companies to transform the original, early product ideas ("nothing") into "something"; which is a product with full clinical utility that will help to improve health and well-being.The web site should use the visual feel of the logo (attached), be modern, simple and clean looking and represent creativity, innovation, scientific thinking and progress.
Updates

Wix Design is acceptable

Industry/Entity Type

Biotechnology

Coding

Coded - Design and coding required

Number of Pages Required

1 page

Font styles to use
Sans Serif

Requirements
Must have
• simple, clean look couple of pages
Should not have
• a lot of pages

```html
<!DOCTYPE html>
<html lang="en">
<head>
<meta charset="utf-8">
<title>Verantel Dx — Consulting for Medical Diagnostics</title>
<link href="https://fonts.googleapis.com/css2?family=Montserrat:wght@400;500;600;700&display=swap" rel="stylesheet">
<style>
:root{
  --blue:#1e73d8;
  --ink:#1c1c1c;
  --muted:#6b6f76;
  --pale:#e9f1fb;
  --white:#ffffff;
  --footer:#363d4a;
}
*{box-sizing:border-box;margin:0;padding:0}
html,body{width:1200px;height:3003px;overflow:hidden}
body{position:relative;font-family:"Montserrat",sans-serif;color:var(--ink);background:var(--white)}
.abs{position:absolute}
.blue{color:var(--blue)}

/* hero */
.hero{left:0;top:0;width:1200px;height:706px;
  background:linear-gradient(100deg,#3d5676 0%,#5a7594 40%,#6d86a3 65%,#8d9db2 100%);
  clip-path:polygon(0 0,1200px 0,1200px 608px,0 706px)}
.hero-glow{left:0;top:0;width:1200px;height:706px;
  background:radial-gradient(ellipse at 85% 30%,rgba(230,220,215,.45),transparent 45%),
             radial-gradient(ellipse at 30% 40%,rgba(150,180,210,.35),transparent 50%);
  clip-path:polygon(0 0,1200px 0,1200px 608px,0 706px)}
.logo{left:141px;top:23px;width:95px;height:93px;border:2px solid var(--blue);color:#fff;
  font-size:21px;font-weight:500;display:flex;align-items:center;padding-left:13px;white-space:nowrap}
.nav{left:461px;top:50px;display:flex;font-size:17px;color:#fff}
.nav a{color:#fff;text-decoration:none;height:37px;line-height:37px;padding:0 17px;margin-right:13px}
.nav a.active{background:var(--blue)}
.hero-title{left:0;width:1200px;top:218px;text-align:center;color:#fff;font-size:64px;line-height:76px;font-weight:700;letter-spacing:1px}
.hero-sub{left:0;width:1200px;top:300px;text-align:center;color:var(--blue);font-size:46px;line-height:56px;font-weight:500;letter-spacing:1px}
.hero-text{left:210px;width:780px;top:372px;text-align:center;color:#fff;font-size:15.5px;line-height:23px}
.btn{background:var(--blue);color:#fff;font-size:14px;display:flex;align-items:center;justify-content:center}

/* about */
.about-bg{left:0;top:600px;width:1200px;height:672px;background:var(--pale);z-index:-1}
.about-frame{left:141px;top:790px;width:419px;height:409px;border:3px solid var(--blue)}
.about-img{left:190px;top:755px;width:410px;height:403px;
  background:radial-gradient(circle at 45% 40%,#6c7fd6,#2b3f9a 45%,#0d1b4a 90%)}
.sec-head{font-size:27px;font-weight:500;padding:18px 0 0 25px;height:66px;white-space:nowrap}
.sec-head::before{content:"";position:absolute;left:0;top:0;width:60px;height:100%;
  border:2px solid var(--blue);border-right:0}
.sec-head::after{content:"";position:absolute;left:58px;top:0;width:2px;height:14px;background:var(--blue)}
.about-text{left:643px;top:905px;width:420px;font-size:13.5px;line-height:25.5px;color:#333}

/* why */
.card{background:#fff;box-shadow:0 2px 12px rgba(0,0,0,.08);text-align:center}
.why-card{top:1450px;width:282px;height:262px}
.why-card .icon{position:absolute;left:106px;top:57px;width:70px;height:70px;border:2px solid var(--blue);
  display:flex;align-items:center;justify-content:center}
.why-card h3{position:absolute;left:0;width:100%;top:148px;font-size:16.5px;font-weight:500}
.why-card p{position:absolute;left:26px;width:230px;top:176px;font-size:11.5px;line-height:19px;color:var(--muted)}

/* reviews */
.reviews-bg{left:0;top:1797px;width:1200px;height:480px;
  background:linear-gradient(90deg,#cfdbe7 0%,#e7eef5 35%,#eef2f6 60%,#d7dfe6 100%)}
.review{top:2020px;width:295px;height:185px;background:rgba(255,255,255,.85);box-shadow:none}
.avatar{top:1983px;width:82px;height:82px;border:2px solid var(--blue);
  background:linear-gradient(180deg,#c8d2dc,#5b6674)}
.review p{position:absolute;left:16px;width:263px;top:62px;font-size:12.5px;line-height:19.5px;color:var(--muted)}
.review .name{position:absolute;left:0;width:100%;top:148px;font-size:15px;color:var(--blue);font-weight:500}

/* partners */
.partner{top:2463px;width:210px;height:120px;display:flex;align-items:center;justify-content:center;gap:10px;
  font-size:22px;font-weight:600}
.partner i{display:block;width:34px;height:34px;border-radius:50%}

/* footer */
.footer{left:0;top:2666px;width:1200px;height:337px;
  background:radial-gradient(ellipse at 72% 40%,#4b5566,transparent 55%),var(--footer)}
.f-logo{left:143px;top:2730px;width:77px;height:76px;border:2px solid var(--blue);color:#fff;font-size:17px;
  display:flex;align-items:center;padding-left:10px;white-space:nowrap}
.f-about{left:141px;top:2813px;width:200px;font-size:12px;line-height:19.5px;color:#fff}
.f-col h4{color:var(--blue);font-size:16px;font-weight:600;margin-bottom:17px}
.f-col ul{list-style:none;color:#fff;font-size:12px;line-height:26px}
.contact-row{display:flex;gap:12px;margin-bottom:22px;color:#fff;font-size:14px;line-height:18px}
.contact-row small{font-size:12px}
.c-icon{width:37px;height:37px;border:2px solid var(--blue);display:flex;align-items:center;justify-content:center}
.follow li{display:flex;gap:14px;align-items:center;line-height:35px}
.follow i{display:block;width:12px;height:12px;border-radius:50%;background:#fff}
.f-rule{left:141px;top:2910px;width:918px;height:1px;background:rgba(255,255,255,.12)}
.copy{left:0;width:1200px;top:2937px;text-align:center;color:#d5d8de;font-size:11px}
</style>
</head>
<body>

<section>
  <div class="abs hero" role="img" aria-label="Scientist in a lab coat viewing x-ray scans on a display"></div>
  <div class="abs hero-glow"></div>
  <div class="abs logo">Verantel&nbsp;<span class="blue">Dx</span></div>
  <nav class="abs nav">
    <a class="active">Home</a><a>About us</a><a>Services</a><a>Innovations</a><a>Contact Us</a>
  </nav>
  <h1 class="abs hero-title">we serve</h1>
  <h2 class="abs hero-sub">Medical Diagnostics Industry</h2>
  <p class="abs hero-text">Lorem ipsum dolor sit amet, consectetuer adipiscing elit, sed diam nonummy nibh euismod tincidunt ut laoreet dolore magna aliquam erat volutpat. Ut wisi enim ad minim veniam, quis nostrud exerci tation ullamcorper suscipit lobortis.</p>
  <div class="abs btn" style="left:535px;top:475px;width:130px;height:37px">Read More</div>
</section>

<section>
  <div class="abs about-bg"></div>
  <div class="abs about-frame"></div>
  <div class="abs about-img" role="img" aria-label="Illustration of a stethoscope with a DNA helix and brain"></div>
  <div class="abs sec-head" style="left:643px;top:812px">About <span class="blue">Verantel Dx</span></div>
  <p class="abs about-text">We are a Biotech consulting firm and we will serve medical diagnostics industry, which is part of the life science/healthcare industry focusing on developing and marketing products that help in early detection, monitoring or management of diseases.</p>
  <div class="abs btn" style="left:643px;top:1071px;width:130px;height:37px">Read More</div>
</section>

<section>
  <div class="abs sec-head" style="left:505px;top:1343px">Why <span class="blue">Choose Us</span></div>
  <div class="abs card why-card" style="left:140px">
    <div class="icon"><svg width="44" height="44" viewBox="0 0 44 44" fill="none" stroke="#222" stroke-width="1.6"><circle cx="22" cy="22" r="19"/><path d="M18 10h8v8h8v8h-8v8h-8v-8h-8v-8h8z"/></svg></div>
    <h3>Medical Diagnostics</h3>
    <p>Lorem Ipsum is simply dummy text of the printing and typesetting industry.</p>
  </div>
  <div class="abs card why-card" style="left:460px">
    <div class="icon"><svg width="44" height="44" viewBox="0 0 44 44" fill="none" stroke="#222" stroke-width="1.6"><circle cx="17" cy="17" r="12"/><circle cx="17" cy="17" r="8"/><path d="M14 17h6M17 14v6M26 26l12 12"/></svg></div>
    <h3>Early Detection</h3>
    <p>Lorem Ipsum is simply dummy text of the printing and typesetting industry.</p>
  </div>
  <div class="abs card why-card" style="left:777px">
    <div class="icon"><svg width="44" height="44" viewBox="0 0 44 44" fill="none" stroke="#222" stroke-width="1.6"><rect x="9" y="7" width="26" height="33"/><rect x="16" y="4" width="12" height="6"/><circle cx="22" cy="16" r="4"/><path d="M13 25h5v4h-5zM13 32h5v4h-5zM21 27h10M21 34h10"/></svg></div>
    <h3>Management of Diseases</h3>
    <p>Lorem Ipsum is simply dummy text of the printing and typesetting industry.</p>
  </div>
</section>

<section>
  <div class="abs reviews-bg" role="img" aria-label="Soft-focus photo of a researcher working in a laboratory"></div>
  <div class="abs sec-head" style="left:468px;top:1867px">Customer <span class="blue">Reviews</span></div>
  <div class="abs card review" style="left:141px"><p>Lorem ipsum dolor sit amet, consectetuer adipiscing elit, sed diam nonummy nibh euismod tincidunt ut laoreet dolore magna aliquam erat volutpat.</p><div class="name">Emma</div></div>
  <div class="abs card review" style="left:453px"><p>Lorem ipsum dolor sit amet, consectetuer adipiscing elit, sed diam nonummy nibh euismod tincidunt ut laoreet dolore magna aliquam erat volutpat.</p><div class="name">Emma</div></div>
  <div class="abs card review" style="left:765px"><p>Lorem ipsum dolor sit amet, consectetuer adipiscing elit, sed diam nonummy nibh euismod tincidunt ut laoreet dolore magna aliquam erat volutpat.</p><div class="name">Emma</div></div>
  <div class="abs avatar" style="left:247px" role="img" aria-label="Customer portrait photo"></div>
  <div class="abs avatar" style="left:559px" role="img" aria-label="Customer portrait photo"></div>
  <div class="abs avatar" style="left:871px" role="img" aria-label="Customer portrait photo"></div>
</section>

<section>
  <div class="abs sec-head" style="left:502px;top:2346px">Our <span class="blue">Partners</span></div>
  <div class="abs card partner" style="left:142px;color:#e0541f">Corvane<i style="background:#e88a2a"></i></div>
  <div class="abs card partner" style="left:377px;color:#5b6b80"><i style="background:#1e73d8"></i>Halden</div>
  <div class="abs card partner" style="left:612px;color:#1f9a6e">Mirola<i style="background:#1f9a6e"></i></div>
  <div class="abs card partner" style="left:847px;color:#2d3a4a"><i style="background:#f0a11f"></i>Ostrix</div>
</section>

<footer>
  <div class="abs footer" role="img" aria-label="Dark photo of a hand touching a digital medical interface"></div>
  <div class="abs f-logo">Verantel&nbsp;<span class="blue">Dx</span></div>
  <p class="abs f-about">Lorem ipsum dolor sit amet, consectetuer adipiscing elit, sed diam.</p>
  <div class="abs f-col" style="left:453px;top:2728px">
    <h4>Quick Link</h4>
    <ul><li>Home</li><li>About Us</li><li>Services</li><li>Innovations</li><li>Contact Us</li></ul>
  </div>
  <div class="abs f-col" style="left:669px;top:2728px">
    <h4>Contact Us</h4>
    <div class="contact-row"><div class="c-icon"><svg width="18" height="18" viewBox="0 0 24 24" fill="#fff"><path d="M6.6 10.8a15 15 0 006.6 6.6l2.2-2.2c.3-.3.7-.4 1-.2 1.1.4 2.3.6 3.6.6.6 0 1 .4 1 1V20c0 .6-.4 1-1 1A17 17 0 013 4c0-.6.4-1 1-1h3.5c.6 0 1 .4 1 1 0 1.3.2 2.5.6 3.6.1.3 0 .7-.2 1z"/></svg></div><div>Phone<br><small>+1 215 555 0142</small></div></div>
    <div class="contact-row"><div class="c-icon"><svg width="18" height="14" viewBox="0 0 18 14" fill="#fff"><path d="M0 1l9 6 9-6V0H0zM0 3v11h18V3l-9 6z"/></svg></div><div>Email<br><small>info@verantelhealth.net</small></div></div>
  </div>
  <div class="abs f-col follow" style="left:966px;top:2728px">
    <h4>Follow Us</h4>
    <ul><li><i></i>Friendsheet</li><li><i></i>Chirper</li></ul>
  </div>
  <div class="abs f-rule"></div>
  <p class="abs copy">© 2019 <span style="color:#fff">Verantel Dx.</span> All rights reserved.</p>
</footer>

</body>
</html>
```